Corporate Design für Steuerkanzlei
Zielgruppe
Wir sind eine Steuerkanzlei im (ländlichen) Neustadt an der Donau, die seit über 30 Jahren von Herrn Konrad (Vater) Wehrle geführt wird. Mit Einstieg durch Herrn Florian (Sohn) Wehrle haben wir die Wehrle Steuerberatungsgellschaft mbH gegründet und suchen deshalb ein neues Kanzleilogo / Geschäftspapiere. Wir betreuen/beraten kleine Unternehmen und Privatpersonen aus der Region und haben derzeitig 14 Angestellte.
Aufgabenstellung
Das Design sollte in erster Linie seriös und nicht verspielt wirken. Einer vertrauensvollen Steuerberaterungskanzlei entsprechend. Dennoch sind wir auch für eine moderne Gestaltung offen.

```html
<!DOCTYPE html>
<html lang="de">
<head>
<meta charset="utf-8">
<title>Wehrle Steuerberatungsgesellschaft mbH – Geschäftsausstattung</title>
<link href="https://fonts.googleapis.com/css2?family=Oswald:wght@300;400;500&family=Open+Sans:wght@400;600;700&family=Arimo:wght@400&display=swap" rel="stylesheet">
<style>
  :root {
    --bg: #2c3138;
    --paper: #ffffff;
    --teal: #177a8b;
    --teal-dark: #0f4f5c;
    --navy: #03212d;
    --ink: #2a2a2a;
    --ink-soft: #3c3c3c;
    --white: #ffffff;
  }
  * { margin: 0; padding: 0; box-sizing: border-box; }
  html, body { width: 1200px; height: 848px; overflow: hidden; }
  body { background: var(--bg); position: relative; font-family: "Open Sans", sans-serif; }

  /* Wordmark */
  .wordmark { position: absolute; display: flex; align-items: center; gap: 6px; }
  .wordmark__square { flex: none; background: var(--teal); }
  .wordmark__text { font-family: "Oswald", sans-serif; font-weight: 400; line-height: 1.05; }
  .wordmark__name { display: block; }
  .wordmark__sub { display: block; font-weight: 300; letter-spacing: .03em; }

  /* Letterhead */
  .letter { position: absolute; left: 172px; top: 64px; width: 509px; height: 720px; background: var(--paper); box-shadow: 0 6px 18px rgba(0,0,0,.35); }
  .letter .wordmark { right: 32px; top: 30px; }
  .letter .wordmark__square { width: 24px; height: 24px; }
  .letter .wordmark__text { color: var(--teal-dark); }
  .letter .wordmark__name { font-size: 20px; }
  .letter .wordmark__sub { font-size: 7.4px; }

  .sender-line { position: absolute; left: 55px; top: 111px; font-family: "Arimo", sans-serif; font-size: 5.6px; color: var(--teal-dark); border-bottom: .6px solid var(--teal); padding: 0 1px 1px; }
  .recipient { position: absolute; left: 55px; top: 130px; font-family: "Arimo", sans-serif; font-size: 8.3px; line-height: 10.3px; color: var(--ink); font-style: normal; }
  .recipient .city { margin-top: 10px; }
  .subject { position: absolute; left: 55px; top: 245px; font-size: 7.8px; font-weight: 700; color: var(--ink); }
  .body-text { position: absolute; left: 55px; top: 273px; width: 278px; font-size: 7.6px; line-height: 9.25px; color: var(--ink-soft); }
  .body-text p + p { margin-top: 9px; }
  .closing { position: absolute; left: 55px; top: 504px; font-size: 7.6px; color: var(--ink-soft); }
  .signature { position: absolute; left: 55px; top: 524px; width: 108px; height: 22px; background: linear-gradient(90deg, rgba(20,20,20,.10), rgba(20,20,20,.04)); border-radius: 3px; }
  .signer { position: absolute; left: 55px; top: 555px; font-size: 7.6px; color: var(--ink-soft); }

  .letter-footer { position: absolute; left: 0; bottom: 0; width: 415px; height: 56px; background: var(--teal); color: var(--white); font-family: "Oswald", sans-serif; font-weight: 300; font-size: 6.6px; line-height: 10.3px; letter-spacing: .12em; }
  .letter-footer .col { position: absolute; top: 13px; }
  .letter-footer .col--person { left: 55px; }
  .letter-footer .col--contact { left: 174px; }
  .letter-footer .col--bank { left: 304px; }

  /* Business cards */
  .card { position: absolute; width: 274px; box-shadow: 0 5px 14px rgba(0,0,0,.4); overflow: hidden; }
  .card--front { left: 767px; top: 198px; height: 175px; background: var(--paper); }
  .card--front .wordmark { left: 21px; top: 21px; gap: 8px; }
  .card--front .wordmark__square { width: 38px; height: 38px; }
  .card--front .wordmark__text { color: var(--teal-dark); }
  .card--front .wordmark__name { font-size: 28px; }
  .card--front .wordmark__sub { font-size: 10px; }
  .card-contact { position: absolute; left: 60px; top: 83px; right: 0; bottom: 0; background: var(--teal); color: var(--white); font-family: "Oswald", sans-serif; font-weight: 300; font-size: 8.6px; letter-spacing: .06em; padding: 8px 0 0 11px; line-height: 11.6px; }
  .card-contact .name, .card-contact .web { font-weight: 500; }
  .card-contact .dot { display: inline-block; width: 3px; height: 3px; background: var(--white); vertical-align: middle; margin: 0 4px; }

  .card--back { left: 766px; top: 475px; height: 177px; background: var(--navy); }
  .card--back .wordmark { left: 63px; top: 72px; gap: 7px; }
  .card--back .wordmark__square { width: 30px; height: 30px; }
  .card--back .wordmark__text { color: var(--white); }
  .card--back .wordmark__name { font-size: 22px; }
  .card--back .wordmark__sub { font-size: 7.4px; }
</style>
</head>
<body>

<section class="letter" aria-label="Briefbogen">
  <div class="wordmark">
    <span class="wordmark__square"></span>
    <span class="wordmark__text"><span class="wordmark__name">Wehrle</span><span class="wordmark__sub">Steuerberatungsgesellschaft mbH</span></span>
  </div>

  <div class="sender-line">Max Mustermann, Musterstr. 123, 12345 Mustetrstadt</div>

  <address class="recipient">
    <div>Martina Musterfrau</div>
    <div>Musterstraße 456</div>
    <div class="city">12345 Berlin</div>
  </address>

  <div class="subject">Quidero molore, atatur sae. Nequat,</div>

  <div class="body-text">
    <p>Ur sit, imus, ipicatem voluptate eum re dolluptios sequosam, eum reritati am volor sapedissi quo blaboribust, sequass itasped igendi cus exerfer fe­ruptas iusanda ndaest, qui omnis nus aut fugitinis quatur ad ullaut mostem quasperiae corem et aciatem illatin ciduntores quidis utemquam autem­perae soluptiae lab illacescia solorum et fugiam ratatatus exerro blaciis samusam etur? Uga. Neque nam simi, nest, ommod essedios magnatia nossi aute nonsequam fugiaspis moluptas sed el int etur saepe nonseca­tem excea noneceperrum ulligendit faccullores et lantur si ium at.Ota cuptae non ea de opta voles rem rae dolore ilia vellab isi blanis idit veribus auda alit labore desenis imenis que in con rehent, explat ped que volorum, autent, si tetur?</p>
    <p>Ihil ium restior ecepero reptistius es aborepe diatiunt dignis diciae voluptu ribearit, que nat aute et as maximus, qui blab iur aut volest, nonsequae odios doluptatiae velignimin perescia vent.<br>Pa voluptas expero corectur molest eaquid enda vidus verciis quodi te dit aliquid unturem poreper feratur? Quis aut rehenihilit et quam, eris et per­orru mquamusa quo et untia volupie nisimoluptae esseribus cora doluptati doluptatur atisciumqui re pa quat aut lam solescia intiis et millabor sit odis et quos re sam, vendicientur abo. Equi totatus rest, nosam quodi omni doloriosam des ea nimpelique volo elendae dellign ihilitis solupta temporp orupta iuntia ipiste natibusapis volesedis reriori taerrup tatiberes nobitiur, sequi omnihillab id maximagnat omnimus dolo quunt, int aut earum lacit peliquunt iduciet, id que autemolum deruptati te non re.</p>
  </div>

  <div class="closing">Sincerely</div>
  <div class="signature" role="img" aria-label="Handschriftliche Unterschrift"></div>
  <div class="signer">Max Mustermann</div>

  <footer class="letter-footer">
    <div class="col col--person">Max Mustermann<br>Musterstr. 123<br>12345 Musterstadt</div>
    <div class="col col--contact">T: 030 / 987 654 321<br>F: 030 / 987 654 322<br>info@firma-beispiel.de</div>
    <div class="col col--bank">Regionalbank GmbH<br>IBAN: DE98765432100<br>BIC: REG812KB44</div>
  </footer>
</section>

<section class="card card--front" aria-label="Visitenkarte Vorderseite">
  <div class="wordmark">
    <span class="wordmark__square"></span>
    <span class="wordmark__text"><span class="wordmark__name">Wehrle</span><span class="wordmark__sub">Steuerberatungsgesellschaft mbH</span></span>
  </div>
  <div class="card-contact">
    <div class="name">Max Mustermann</div>
    <div>Geschäftsführer</div>
    <div>Musterstr. 123<span class="dot"></span>12345 Musterstadt</div>
    <div>T: 030 / 987 654 321 &nbsp; F: 030 / 987 654 323</div>
    <div>info@kanzlei-beispiel.de</div>
    <div class="web">www.kanzlei-beispiel.de</div>
  </div>
</section>

<section class="card card--back" aria-label="Visitenkarte Rückseite">
  <div class="wordmark">
    <span class="wordmark__square"></span>
    <span class="wordmark__text"><span class="wordmark__name">Wehrle</span><span class="wordmark__sub">Steuerberatungsgesellschaft mbH</span></span>
  </div>
</section>

</body>
</html>
```